Irrigation Business needs their business cards modernised and revamped

I would like to keep my current logo, colours and revamp the format of the card.

I would like the card to be clean yet important.

Im not sure if you include texture but i would like the named logo to be indented into the card etc.

show me something alive and free something thats clinical to the point yet has a feel of achievement. i would like people to go nice card.

Target Market(s)

high end clients, corporate, sports field manger, the guys that make the decisions

Industry/Entity Type

Business

Contact Information for Business Card

nformation to be included

Dean Harlow (Director)
0487305526
dean@kolvat.biz
www.kestonfieldworks.com

instagram logo
google logo
facebook logo

Colors

Designer to choose colors to be used in the design.

Requirements
Nice to have
• indentations a really nice feel to the card good texture

```html
<!DOCTYPE html>
<html lang="en">
<head>
<meta charset="utf-8">
<title>Keston Fieldworks – Business Card</title>
<link rel="stylesheet" href="https://fonts.googleapis.com/css2?family=Open+Sans:wght@400;600;700;800&display=swap">
<style>
  :root {
    --backdrop: #2b2c2e;
    --card-white: #fbfbfb;
    --brand-blue: #1f5fae;
    --brand-blue-deep: #154a92;
    --brand-sky: #3c8fd6;
    --brand-green: #3aa55a;
    --halo: rgba(232, 240, 248, 0.9);
    --halo-ring: rgba(255, 255, 255, 0.75);
    --ink-light: #ffffff;
  }
  * { box-sizing: border-box; margin: 0; padding: 0; }
  html, body {
    width: 1200px; height: 840px; overflow: hidden;
    background: var(--backdrop);
    font-family: "Open Sans", Arial, sans-serif;
  }
  .sheet {
    width: 1200px; height: 840px;
    display: flex; flex-direction: column;
    align-items: center; justify-content: center; gap: 40px;
  }
  .card {
    position: relative;
    width: 620px; height: 354px;
    background: var(--card-white);
    overflow: hidden;
    box-shadow: 0 10px 28px rgba(0,0,0,0.35);
  }

  /* Front */
  .card--front {
    display: flex; flex-direction: column;
    align-items: center; justify-content: center;
  }
  .brand-mark {
    width: 72px; height: 72px; border-radius: 50%;
    background: var(--brand-sky);
    margin-bottom: 14px;
  }
  .brand-name {
    font-weight: 800; font-size: 34px; letter-spacing: 0.5px;
    color: var(--brand-blue);
    line-height: 1;
  }
  .social-row {
    display: flex; gap: 8px; margin-top: 18px;
  }
  .social-dot {
    width: 18px; height: 18px; border-radius: 50%;
    background: var(--brand-blue);
  }

  /* Back */
  .card--back .band {
    position: absolute; inset: 0; width: 100%; height: 100%;
  }
  .halo {
    position: absolute;
    right: -10px; top: 18px;
    width: 300px; height: 300px; border-radius: 50%;
    background: var(--halo);
    border: 6px solid var(--halo-ring);
    display: flex; align-items: center; justify-content: center;
  }
  .halo .brand-name { font-size: 22px; }
  .person {
    position: absolute; left: 58px; top: 138px;
  }
  .person__name {
    font-weight: 700; font-size: 17px; color: var(--brand-blue);
    text-transform: uppercase; letter-spacing: 0.2px;
  }
  .person__role {
    font-weight: 600; font-size: 15px; color: var(--brand-green);
    text-transform: uppercase; margin-top: 2px;
  }
  .contact-list {
    position: absolute; left: 58px; bottom: 40px;
    list-style: none; color: var(--ink-light);
    font-size: 15px; line-height: 1.45;
  }
  .contact-list li { display: flex; align-items: center; gap: 10px; }
  .contact-icon { width: 14px; height: 14px; flex: none; }
</style>
</head>
<body>
<main class="sheet">

  <section class="card card--front" aria-label="Card front">
    <div class="brand-mark" aria-hidden="true"></div>
    <div class="brand-name">KESTON FIELDWORKS</div>
    <div class="social-row" aria-label="Social profiles">
      <span class="social-dot"></span>
      <span class="social-dot"></span>
      <span class="social-dot"></span>
    </div>
  </section>

  <section class="card card--back" aria-label="Card back">
    <svg class="band" viewBox="0 0 620 354" preserveAspectRatio="none" aria-hidden="true">
      <defs>
        <linearGradient id="bandFill" x1="0" y1="0" x2="1" y2="1">
          <stop offset="0" stop-color="#2468b8"/>
          <stop offset="1" stop-color="#154a92"/>
        </linearGradient>
      </defs>
      <polygon points="0,222 620,92 620,354 0,354" fill="url(#bandFill)"/>
    </svg>

    <div class="halo">
      <div class="brand-name">KESTON FIELDWORKS</div>
    </div>

    <div class="person">
      <div class="person__name">Dean Harlow</div>
      <div class="person__role">Director</div>
    </div>

    <ul class="contact-list">
      <li>
        <svg class="contact-icon" viewBox="0 0 16 16" aria-hidden="true">
          <path d="M4 1.5l2.4 2.6-1.3 1.7c.9 2 2.3 3.5 4.2 4.4l1.7-1.3 2.6 2.4-1.5 2.4C7 13.3 2.6 8.9 1.6 3z" fill="#fff"/>
        </svg>
        <span>0487305526</span>
      </li>
      <li>
        <svg class="contact-icon" viewBox="0 0 16 16" aria-hidden="true">
          <rect x="1" y="3" width="14" height="10" rx="1" fill="#fff"/>
          <path d="M1.5 3.8L8 9l6.5-5.2" fill="none" stroke="#1f5fae" stroke-width="1.4"/>
        </svg>
        <span>dean@kolvat.biz</span>
      </li>
      <li>
        <svg class="contact-icon" viewBox="0 0 16 16" aria-hidden="true">
          <circle cx="8" cy="8" r="6.5" fill="none" stroke="#fff" stroke-width="1.4"/>
          <ellipse cx="8" cy="8" rx="2.8" ry="6.5" fill="none" stroke="#fff" stroke-width="1.2"/>
          <path d="M1.5 8h13" stroke="#fff" stroke-width="1.2"/>
        </svg>
        <span>www.kestonfieldworks.com</span>
      </li>
    </ul>
  </section>

</main>
</body>
</html>
```